Velundra Jobs portal

Velundra Jobs is a job portal connecting job seekers and companies offering part time jobs in the Mena region, starting in the UAE. We would like to see designs that use the color blue. We have attached images to give an idea what the website should look like. When a company posts a job the job seekers are not allowed to see which company has posted a job. There should also be a coinvex gateway. On the landing page we want a catching picture that we will send.

Target Market(s)

Students and promotional workers

Logo Text

Velundra Jobs

Coding

Coded - Design and coding required

Number of Pages Required

4 page

Font styles to use
Sans Serif

Colors
33a6d7
0692cd
85cae6

```html
<!DOCTYPE html>
<html lang="en">
<head>
<meta charset="utf-8">
<title>Velundra Jobs</title>
<link href="https://fonts.googleapis.com/css2?family=Open+Sans:wght@400;600&family=Jost:wght@400;500;600&display=swap" rel="stylesheet">
<style>
:root{
  --blue:#3465b1;
  --blue-dark:#2a55a3;
  --blue-light:#4b7fc9;
  --teal:#52c2c6;
  --pink:#e2427f;
  --pink-dark:#d6336f;
  --text:#444;
  --muted:#666;
  --panel:#e8e8e8;
  --line:#dcdcdc;
  --page:#f6f6f6;
}
*{box-sizing:border-box;margin:0;padding:0}
html,body{width:1200px;height:1041px;overflow:hidden}
body{position:relative;background:var(--page);font-family:"Open Sans",sans-serif;color:var(--text)}
.abs{position:absolute}
.topline{left:0;top:0;width:1200px;height:7px;background:var(--blue)}
.header{left:0;top:7px;width:1200px;height:114px;background:linear-gradient(#fff,#f3f3f3);border-bottom:1px solid #e2e2e2}
.brand{left:98px;top:22px;font-family:"Jost",sans-serif;font-weight:400;font-size:52px;color:var(--teal);letter-spacing:-1px}
.nav a{position:absolute;top:51px;font-family:"Jost",sans-serif;font-weight:500;font-size:14px;color:#333;text-decoration:none}
.avatar{left:949px;top:39px;width:40px;height:40px;border-radius:50%;background:linear-gradient(#8a5a3c,#c99a7a)}
.badge{left:917px;top:42px;width:18px;height:18px;border-radius:50%;background:var(--pink);color:#fff;font-size:10px;text-align:center;line-height:18px}
.logout{left:1004px;top:44px;width:96px;height:33px;background:linear-gradient(var(--blue-light),var(--blue-dark));color:#fff;font-family:"Jost",sans-serif;font-weight:500;font-size:14px;text-align:center;line-height:33px;border-radius:3px}

.sidebar{left:98px;top:163px;width:245px;height:397px;background:var(--panel);border:1px solid #ddd}
.sidebar h2{height:55px;background:linear-gradient(var(--blue-light),var(--blue-dark));color:#fff;font-family:"Jost",sans-serif;font-weight:500;font-size:18px;line-height:55px;padding-left:20px}
.cats{list-style:none;padding-top:20px}
.cats li{height:31px;font-size:14.5px;color:#333;padding-left:38px;position:relative}
.cats li::before{content:"";position:absolute;left:18px;top:6px;border-left:4px solid #222;border-top:3.5px solid transparent;border-bottom:3.5px solid transparent}

.filter{left:396px;top:161px;width:706px;height:100px;background:#f0f0f0;border:1px solid #e2e2e2}
.field{top:32px;height:39px;background:#fff;border:1px solid #e2e2e2;font-size:13px;color:#333;line-height:37px;padding-left:15px}
.filter-btn{left:575px;top:31px;width:107px;height:39px;background:linear-gradient(#ea5b92,var(--pink-dark));border-radius:3px;color:#fff;font-family:"Jost",sans-serif;font-weight:500;font-size:15px;letter-spacing:.5px;text-align:center;line-height:39px}

.jobs{left:397px;top:283px;width:704px;height:347px;background:#fff;border:1px solid #e2e2e2;overflow:hidden}
.jobs .hrow{height:53px;background:linear-gradient(var(--blue-light),var(--blue-dark))}
.jobs .hrow span{position:absolute;top:0;line-height:53px;color:#fff;font-family:"Jost",sans-serif;font-weight:500;font-size:15px}
.row{position:absolute;left:0;width:696px;height:73px}
.row.active{background:var(--teal)}
.row span{position:absolute;top:0;line-height:73px;font-size:12.5px;color:var(--text)}
.row .title{left:23px;font-size:14.5px;color:var(--muted)}
.row.active span{color:#fff}
.apply{position:absolute;left:560px;top:15px;width:96px;height:35px;border-radius:3px;background:linear-gradient(var(--blue-light),var(--blue-dark));color:#fff;font-size:13px;font-weight:600;text-align:center;line-height:35px}
.row.active .apply{background:linear-gradient(#ea5b92,var(--pink-dark))}
.col{position:absolute;top:0;width:1px;height:347px;background:var(--line)}
.scroll{left:696px;top:53px;width:8px;height:294px;background:#f4f4f4}
.scroll i{position:absolute;left:2px;top:2px;width:4px;height:76px;background:#555}

.mascot{left:81px;top:617px;width:228px;height:304px;border-radius:40% 40% 30% 30%;background:radial-gradient(ellipse at 50% 40%,rgba(190,215,235,.35),rgba(240,240,240,0) 70%)}

.featured{left:397px;top:670px;font-family:"Jost",sans-serif;font-weight:500;font-size:30px;color:var(--pink)}
.arrow{top:680px;width:22px;height:22px;border-radius:50%;background:linear-gradient(#fff,#ddd);border:1px solid #bbb}
.photo{top:729px;width:164px;height:126px;border:1px solid #ddd}
.caption{top:870px;font-size:13.5px;color:var(--muted)}

.footer{left:0;top:927px;width:1200px;height:114px;background:var(--blue);color:#fff}
.copy{left:98px;top:40px;font-size:12.5px}
.flinks{left:99px;top:70px;font-size:11.5px;word-spacing:1px}
.social{top:55px;width:19px;height:19px;background:#fff;border-radius:4px}
</style>
</head>
<body>
<div class="abs topline"></div>
<header class="abs header">
  <div class="abs brand">Velundra</div>
  <nav class="nav"><a style="left:355px">About Us</a><a style="left:443px">Contact Us</a></nav>
  <svg class="abs" style="left:862px;top:51px" width="26" height="26" viewBox="0 0 26 26" aria-label="Search">
    <circle cx="10" cy="10" r="8" fill="none" stroke="#444" stroke-width="2.5"/><line x1="16" y1="16" x2="23" y2="23" stroke="#444" stroke-width="3" stroke-linecap="round"/>
  </svg>
  <svg class="abs" style="left:904px;top:51px" width="28" height="28" viewBox="0 0 28 28" aria-label="Notifications">
    <path d="M7 20V12a7 7 0 0 1 14 0v8l3 3H4z" fill="none" stroke="#444" stroke-width="2"/><circle cx="14" cy="25" r="2.2" fill="#444"/>
  </svg>
  <div class="abs badge">23</div>
  <div class="abs avatar" role="img" aria-label="User profile photo"></div>
  <div class="abs logout">LOG OUT</div>
</header>

<aside class="abs sidebar">
  <h2>CATEGORY</h2>
  <ul class="cats">
    <li>Category 1 (30)</li><li>Category 2 (3)</li><li>Category 3 (23)</li><li>Category 4 (43)</li><li>Category 5 (189)</li>
    <li>Category 6 (43)</li><li>Category 7 (983)</li><li>Category 8 (23)</li><li>Category 9 (143)</li><li>Category 10 (35)</li>
  </ul>
</aside>
<div class="abs mascot" role="img" aria-label="Faint mascot character illustration"></div>

<section class="abs filter">
  <div class="abs field" style="left:23px;width:257px">Keyword</div>
  <div class="abs field" style="left:297px;width:258px">District 1
    <svg class="abs" style="right:14px;top:16px" width="10" height="6" viewBox="0 0 10 6"><path d="M0 0h10L5 6z" fill="#222"/></svg>
  </div>
  <div class="abs filter-btn">FILTER JOB</div>
</section>

<section class="abs jobs">
  <div class="hrow">
    <span style="left:23px">Job Title</span><span style="left:243px">Due Date</span><span style="left:382px">Provider Name</span>
  </div>
  <div class="row" style="top:53px"><span class="title">Front-end Developer</span><span style="left:251px">23-05-15</span><span style="left:402px">Provider 1</span><div class="apply">Apply Now</div></div>
  <div class="row active" style="top:126px"><span class="title">Front-end Developer</span><span style="left:251px">23-05-15</span><span style="left:402px">Provider 1</span><div class="apply">Apply Now</div></div>
  <div class="row" style="top:199px"><span class="title">Front-end Developer</span><span style="left:251px">23-05-15</span><span style="left:402px">Provider 1</span><div class="apply">Apply Now</div></div>
  <div class="row" style="top:272px"><span class="title">Front-end Developer</span><span style="left:251px">23-05-15</span><span style="left:402px">Provider 1</span><div class="apply">Apply Now</div></div>
  <div class="col" style="left:203px"></div><div class="col" style="left:356px"></div><div class="col" style="left:512px"></div>
  <div class="abs scroll"><i></i></div>
</section>

<h2 class="abs featured">Featured Job Providers</h2>
<svg class="abs arrow" style="left:1051px" viewBox="0 0 22 22"><path d="M12.5 6.5L8 11l4.5 4.5" fill="none" stroke="#333" stroke-width="2"/></svg>
<svg class="abs arrow" style="left:1078px" viewBox="0 0 22 22"><path d="M9 6.5l4.5 4.5L9 15.5" fill="none" stroke="#333" stroke-width="2"/></svg>

<div class="abs photo" style="left:399px;background:linear-gradient(135deg,#9b8a80,#e4e2e0)" role="img" aria-label="Photo of a person working with a calculator and documents"></div>
<div class="abs photo" style="left:579px;background:linear-gradient(135deg,#a9b3bd,#e9ecef)" role="img" aria-label="Photo of colleagues in a meeting"></div>
<div class="abs photo" style="left:759px;background:linear-gradient(135deg,#f2f2f2,#9fbbd8)" role="img" aria-label="Photo of a woman using a laptop"></div>
<div class="abs photo" style="left:937px;background:linear-gradient(135deg,#d3b49a,#f1ece8)" role="img" aria-label="Photo of a group of people working together"></div>
<p class="abs caption" style="left:399px">Lorem ipsum dolor sit</p>
<p class="abs caption" style="left:579px">Lorem ipsum dolor sit</p>
<p class="abs caption" style="left:759px">Lorem ipsum dolor sit</p>
<p class="abs caption" style="left:938px">Lorem ipsum dolor sit</p>

<footer class="abs footer">
  <p class="abs copy">© 2015 VELUNDRA - ALL RIGHTS RESERVED</p>
  <p class="abs flinks">HOME &nbsp;|&nbsp; ABOUT US &nbsp;|&nbsp; TERMS &amp; CONDITIONS &nbsp;|&nbsp; SITE MAP &nbsp;|&nbsp; CONTACT US</p>
  <div class="abs social" style="left:962px"></div>
  <div class="abs social" style="left:992px"></div>
  <div class="abs social" style="left:1022px"></div>
  <div class="abs social" style="left:1052px"></div>
  <div class="abs social" style="left:1082px"></div>
</footer>
</body>
</html>
```